New Business card design to reflect rebrand

I would like a business card design with a good base colour for our new logo and also a placeholder for a profile pic of the card holder. the design needs to be editable to the point that we can easily change the picture of the person and use that design for printmerlo etc. we are looking at a metalic finish business card so will need a good base colour to bring out the finish.

Target Market(s)

prospective customers

Industry/Entity Type

Business

Contact Information for Business Card

I would like one editable design that we can change the name of the card holder and profile picture. The design need to be in a format that be send to printmerlo etc.

Our address is Fenwick Lodge, Copse Lane, Ashcombe Vale, GU14 3TP Tel no. 01483 556172

Requirements
Must have
• place holder for a profile pic for the card holder. in AI or preferably PSD format

```html
<!DOCTYPE html>
<html lang="en">
<head>
<meta charset="utf-8">
<title>Corvane Facility Partners – Business Card</title>
<link rel="stylesheet" href="https://fonts.googleapis.com/css2?family=Open+Sans:wght@400;600;700&display=swap">
<style>
  :root {
    --backdrop: #2b2d31;
    --card-white: #ffffff;
    --brand-slate: #3f4d63;
    --brand-orange: #ec6100;
    --text-light: #ffffff;
    --photo-dark: #23243a;
    --photo-mid: #4a4c5e;
    --photo-light: #c9c4c0;
  }
  * { box-sizing: border-box; margin: 0; padding: 0; }
  html, body {
    width: 1200px; height: 864px; overflow: hidden;
    background: var(--backdrop);
    font-family: "Open Sans", Arial, sans-serif;
  }
  .stage { position: relative; width: 1200px; height: 864px; }
  .card {
    position: absolute; left: 300px; width: 600px; height: 340px;
    border-radius: 3px; overflow: hidden;
  }
  .card--front {
    top: 52px; background: var(--card-white);
    display: flex; align-items: center; justify-content: center;
  }
  .brand-name {
    color: var(--brand-slate); font-weight: 700;
    font-size: 50px; line-height: 1.1; letter-spacing: 3px;
    text-align: center; text-transform: uppercase;
  }
  .brand-name span { display: block; font-size: 20px; letter-spacing: 6px; margin-top: 8px; }
  .card--back { top: 452px; background: var(--brand-orange); }
  .profile-photo {
    position: absolute; left: 0; bottom: 0; width: 250px; height: 310px;
    border-radius: 110px 110px 0 0;
    background: linear-gradient(180deg, var(--photo-light) 0%, var(--photo-mid) 42%, var(--photo-dark) 100%);
  }
  .holder {
    position: absolute; left: 285px; top: 82px; color: var(--text-light);
  }
  .holder-name { font-size: 27px; font-weight: 700; margin-bottom: 24px; }
  .contact-line {
    display: flex; align-items: center; gap: 10px;
    font-size: 17px; margin-bottom: 8px;
  }
  .contact-line svg { width: 14px; height: 14px; fill: var(--text-light); flex: none; }
  .address { font-size: 17px; line-height: 1.35; margin-top: 22px; }
</style>
</head>
<body>
<main class="stage">
  <section class="card card--front" aria-label="Card front">
    <h1 class="brand-name">Corvane<span>Facility Partners</span></h1>
  </section>

  <section class="card card--back" aria-label="Card back">
    <div class="profile-photo" role="img" aria-label="Profile photo of the card holder"></div>
    <div class="holder">
      <h2 class="holder-name">Daniel Reeve</h2>
      <p class="contact-line">
        <svg viewBox="0 0 24 24" aria-hidden="true"><path d="M6.6 10.8a15.1 15.1 0 0 0 6.6 6.6l2.2-2.2a1 1 0 0 1 1-.25 11.4 11.4 0 0 0 3.6.57 1 1 0 0 1 1 1V20a1 1 0 0 1-1 1A17 17 0 0 1 3 4a1 1 0 0 1 1-1h3.5a1 1 0 0 1 1 1c0 1.25.2 2.45.57 3.57a1 1 0 0 1-.25 1z"/></svg>
        01483 556172
      </p>
      <p class="contact-line">
        <svg viewBox="0 0 24 24" aria-hidden="true"><path d="M2 5h20v14H2z M3.5 6.5 12 13l8.5-6.5" fill="none" stroke="#fff" stroke-width="2"/></svg>
        info@corvane.com
      </p>
      <p class="address">Fenwick Lodge, Copse Lane,<br>Ashcombe Vale, GU14 3TP</p>
    </div>
  </section>
</main>
</body>
</html>
```